New start-up company catalog!

Heat transfer printing company. We are set to launch later this month and need a stand out catalog to wow our customers. We are a printing/manufacturing heat transfer company geared towards apparel and promotional items.

```html
<!DOCTYPE html>
<html lang="en">
<head>
<meta charset="utf-8">
<title>Northline Prints – Catalog Spreads</title>
<link rel="stylesheet" href="https://fonts.googleapis.com/css2?family=Montserrat:wght@500;600;700;800&family=Graduate&display=swap">
<style>
  :root{
    --board:#58585a;
    --paper:#ffffff;
    --teal:#3bbfbf;
    --purple:#3e2a8a;
    --purple-2:#6a3aa8;
    --orange:#f7a823;
    --magenta:#e0168a;
    --navy:#2a2670;
    --row:#d6f0f0;
    --ink:#111;
  }
  *{box-sizing:border-box;margin:0;padding:0}
  html,body{width:1022px;height:1200px;overflow:hidden}
  body{background:var(--board);font-family:"Montserrat",sans-serif;position:relative}
  .page{position:absolute;width:451px;height:351px;background:var(--paper);overflow:hidden}
  .page-1{left:37px;top:34px}
  .page-2{left:528px;top:34px}
  .page-3{left:37px;top:426px}
  .page-4{left:528px;top:426px}
  .page-5{left:37px;top:817px}
  .page-mark{position:absolute;bottom:0;width:7px;height:7px;background:var(--magenta)}
  .page-mark.left{left:0}
  .page-mark.right{right:0}
  .bg-shapes{position:absolute;inset:0}

  /* feature page */
  .photo{position:absolute}
  .feature-title{position:absolute;right:16px;text-align:right;color:var(--orange);font-weight:700;font-size:14.5px;line-height:15px;letter-spacing:.3px}
  .feature-title span{background:var(--purple);padding:0 3px;box-decoration-break:clone;-webkit-box-decoration-break:clone}
  .feature-band{position:absolute;left:10px;right:0;background:linear-gradient(90deg,var(--purple),var(--purple-2));display:flex;align-items:center;justify-content:space-between;padding:0 20px 0 10px}
  .feature-band h2{color:#fff;font-weight:600;font-size:13.5px;line-height:16px;letter-spacing:.4px}
  .feature-band p{color:var(--orange);font-weight:600;font-size:6.3px;line-height:8px;width:185px}
  .option-tag{position:absolute;background:var(--teal);color:#fff;font-size:6.5px;font-weight:600;display:flex;align-items:center;padding-left:12px}

  .slider{position:absolute;width:116px;font-size:5.5px;font-weight:600;color:var(--navy)}
  .slider .label{text-align:center;font-size:7.5px;margin-bottom:2px}
  .slider .track{height:3px;background:var(--orange);position:relative;width:104px}
  .slider .track::after{content:"";position:absolute;left:104px;top:-2px;width:11px;height:6px;background:repeating-linear-gradient(90deg,#bbb 0 1px,transparent 1px 2.5px)}
  .slider .ends{display:flex;justify-content:space-between;margin-top:3px}

  .stat{position:absolute;top:290px;width:54px;text-align:center}
  .stat .box{height:40px;border:2.5px solid var(--orange);border-right-color:#bdbdbd;display:flex;flex-direction:column;align-items:center;justify-content:center;color:var(--teal);font-weight:700}
  .stat .num{font-size:19px;line-height:18px}
  .stat .unit{font-size:7px;line-height:8px}
  .stat .cap{color:var(--navy);font-size:7.5px;font-weight:600;margin-top:3px}

  /* pricing page */
  .section-bar{position:absolute;left:0;width:441px;background:linear-gradient(90deg,var(--purple),var(--purple-2));color:#fff}
  .section-bar.main{top:21px;height:18px;font-size:13px;font-weight:600;padding-left:20px;line-height:18px}
  .section-bar.sub{height:18px;font-size:6.3px;font-weight:600;line-height:6.5px;padding:3px 0 0 20px}
  .art-sample{position:absolute;left:40px;top:66px;width:86px;height:66px;border:1px dashed #bbb}
  .dim{position:absolute;font-size:4.5px;color:#333}

  .price{position:absolute;border-collapse:collapse;font-size:4px;width:122px}
  .price th{background:var(--navy);color:#fff;font-weight:600;text-align:left;padding:.6px 1.5px}
  .price td{background:var(--row);color:var(--ink);padding:.4px 1.5px;text-align:center}
  .price td:first-child{text-align:left}

  .no-gang{position:absolute;left:400px;top:140px;text-align:center;font-size:3.5px;color:#333;width:36px}

  .swatches{position:absolute;left:15px;display:flex;gap:4.8px}
  .swatch{width:34px;height:34px;position:relative;color:#fff;font-size:4.8px;font-weight:600;line-height:5px;padding:0 0 1.5px 2px;display:flex;flex-direction:column;justify-content:flex-end}
  .swatch.light{color:#222;border:1px solid #bbb}

  /* numbers page */
  .digits{position:absolute;top:62px;width:104px;display:grid;grid-template-columns:repeat(3,1fr);font-family:"Graduate",serif;font-size:50px;line-height:46px;text-align:center;color:#000}
  .digits.solid{-webkit-text-stroke:2.2px #000}
  .digits .last{grid-column:2}
  .digits.outlined{-webkit-text-stroke:1.1px #fff;text-shadow:1.6px 0 #000,-1.6px 0 #000,0 1.6px #000,0 -1.6px #000,1.2px 1.2px #000,-1.2px -1.2px #000,1.2px -1.2px #000,-1.2px 1.2px #000}
  .origin-badge{position:absolute;left:322px;top:70px;width:80px;height:80px;border-radius:50%;background:#dcdff0;border:3px solid var(--navy)}
  .kit-table{position:absolute;left:302px;top:211px;border-collapse:collapse;font-size:5px;width:116px}
  .kit-table th{background:var(--navy);color:#fff;font-weight:600;padding:.5px 2px}
  .kit-table td{background:var(--row);padding:.3px 2px;text-align:center}

  /* back cover */
  .brand{position:absolute;left:103px;top:150px;display:flex;align-items:center;gap:8px}
  .brand .mark{width:34px;height:34px;background:var(--purple)}
  .brand .name{font-size:31px;font-weight:700;color:var(--purple);letter-spacing:-.3px}
  .tagline{position:absolute;right:14px;top:303px;color:#fff;font-weight:700;font-size:21px;letter-spacing:.3px}
  .contact{position:absolute;right:16px;top:332px;color:var(--orange);font-size:6.5px;font-weight:600}
</style>
</head>
<body>

<!-- Spread 1: nylon & polypro -->
<section class="page page-1">
  <svg class="bg-shapes" viewBox="0 0 451 351" aria-hidden="true">
    <polygon points="0,0 410,0 0,200" fill="var(--teal)"/>
    <polygon points="451,40 451,240 170,240" fill="var(--teal)"/>
  </svg>
  <div class="photo" role="img" aria-label="Promotional products printed with heat transfers: umbrella, duffel bag, folding chair, tote bags" style="left:20px;top:18px;width:300px;height:222px;background:linear-gradient(135deg,#2b2d33 0%,#3c5a8a 35%,#c9262e 60%,#7a7f86 80%,#b98a55 100%);opacity:.9"></div>
  <div class="photo" role="img" aria-label="Jute tote bag" style="left:395px;top:135px;width:50px;height:105px;background:linear-gradient(180deg,#c23a6b,#b98a55)"></div>
  <h1 class="feature-title" style="top:27px">
    <span>NYLON AND</span><br><span>POLYPRO</span><br><span>HEAT</span><br><span>TRANSFERS</span>
  </h1>
  <div class="feature-band" style="top:202px;height:70px">
    <h2>NYLON MATERIAL OR<br>NON-WOVEN/<br>POLYPROPYLENE MATERIAL</h2>
    <p>Looking to expand your product offerings? Look no further! Our Nylon or PolyPro heat transfers are engineered to apply on temperature sensitive products. Low temperature application is quick and easy! Hot peel them in only 7 seconds!</p>
  </div>
  <div class="option-tag" style="left:287px;top:270px;width:164px;height:15px">1, 2, 3 Color or Unlimited color options</div>

  <div class="slider" style="left:23px;top:287px">
    <div class="label">Feel</div>
    <div class="track"></div>
    <div class="ends"><span>Soft</span><span>Heavy</span></div>
  </div>
  <div class="slider" style="left:23px;top:316px">
    <div class="label">Opacity</div>
    <div class="track"></div>
    <div class="ends"><span>Transparent</span><span>Opaque</span></div>
  </div>

  <div class="stat" style="left:176px"><div class="box"><span class="num">7</span><span class="unit">Seconds</span></div><div class="cap">Time</div></div>
  <div class="stat" style="left:245px"><div class="box"><span class="num">325</span><span class="unit">Degrees</span></div><div class="cap">Temprature</div></div>
  <div class="stat" style="left:315px"><div class="box"><span class="num">60</span><span class="unit">PSI</span></div><div class="cap">Pressure</div></div>
  <div class="stat" style="left:383px"><div class="box">
    <svg width="18" height="22" viewBox="0 0 18 22" aria-hidden="true"><path d="M4 20c-3-5 3-7 0-12M9 20c-3-6 3-9 0-16M14 20c-3-5 3-7 0-12" fill="none" stroke="var(--orange)" stroke-width="1.8" stroke-linecap="round"/></svg>
  </div><div class="cap">Hot Peel</div></div>
  <span class="page-mark left"></span>
</section>

<!-- Spread 2: nylon pricing -->
<section class="page page-2">
  <div class="section-bar main">Sizing &amp; Pricing</div>
  <span class="dim" style="left:76px;top:62px">12.75"</span>
  <span class="dim" style="left:30px;top:97px">9"</span>
  <div class="art-sample" role="img" aria-label="Sample navy lettered artwork at 9 by 12.75 inches" style="background:linear-gradient(135deg,#e9edf5,#c9d2e6)"></div>

  <table class="price" style="left:148px;top:69px">
    <tr><th>Nylon 9x12.75</th><th>1 color</th><th>2 color</th><th>3 color</th><th>Process</th></tr>
    <tr><td>144</td><td>n/a</td><td>n/a</td><td>n/a</td><td>$ 2.18</td></tr>
    <tr><td>288</td><td>n/a</td><td>n/a</td><td>n/a</td><td>$ 1.83</td></tr>
    <tr><td>512</td><td>$ 0.59</td><td>$ 1.03</td><td>$ 1.43</td><td>$ 1.33</td></tr>
  </table>
  <table class="price" style="left:148px;top:102px;width:104px">
    <tr><th>Nylon 9x12.75</th><th>Single Image</th><th>Set-up</th></tr>
    <tr><td>1</td><td>$0.15</td><td>$ 20.00</td></tr>
  </table>
  <table class="price" style="left:148px;top:118px">
    <tr><th>PolyPro 9x12.75</th><th>1 color</th><th>2 color</th><th>3 color</th><th>Process</th></tr>
    <tr><td>100</td><td>$ 1.30</td><td>$ 2.05</td><td>$ 2.48</td><td>$ 2.23</td></tr>
    <tr><td>250</td><td>$ 0.57</td><td>$ 0.90</td><td>$ 1.08</td><td>$ 0.98</td></tr>
  </table>
  <table class="price" style="left:276px;top:69px">
    <tr><th>Nylon 19x12.75</th><th>1 color</th><th>2 color</th><th>3 color</th><th>Process</th></tr>
    <tr><td>144</td><td>n/a</td><td>n/a</td><td>n/a</td><td>$ 3.78</td></tr>
    <tr><td>288</td><td>n/a</td><td>n/a</td><td>n/a</td><td>$ 2.83</td></tr>
    <tr><td>512</td><td>$ 0.69</td><td>$ 1.14</td><td>$ 1.73</td><td>$ 1.98</td></tr>
  </table>
  <table class="price" style="left:276px;top:102px;width:122px">
    <tr><th>Nylon 12x12</th><th>Single Image</th><th>Set-up</th></tr>
    <tr><td>1</td><td>$0.20</td><td>$ 22.00</td></tr>
  </table>

  <div class="no-gang">No Art Ganging
    <svg width="34" height="34" viewBox="0 0 34 34" aria-hidden="true" style="display:block;margin:2px auto 0">
      <circle cx="17" cy="17" r="14" fill="none" stroke="#e0242b" stroke-width="2"/>
      <rect x="10" y="11" width="6" height="5" fill="#3aa35a"/><rect x="18" y="18" width="6" height="5" fill="#3aa35a"/>
      <line x1="7" y1="27" x2="27" y2="7" stroke="#e0242b" stroke-width="2"/>
    </svg>
  </div>

  <div class="section-bar sub" style="top:178px">Available Colors:<br>Essential, Nylon</div>
  <div class="swatches" style="top:202px">
    <div class="swatch" style="background:#000">Black</div>
    <div class="swatch" style="background:#9aa0a6">Gray<br>7543C</div>
    <div class="swatch" style="background:#9b2335">Burgundy<br>194C</div>
    <div class="swatch" style="background:#b0202e">Red<br>187C</div>
    <div class="swatch" style="background:#d81b87">Hot Pink<br>232C</div>
    <div class="swatch" style="background:#f49ac1">Pink<br>1905C</div>
    <div class="swatch" style="background:#3a1f6b">Purple<br>2685C</div>
    <div class="swatch" style="background:#1b365d">Navy<br>654C</div>
    <div class="swatch" style="background:#1e3f8f">Royal<br>287C</div>
    <div class="swatch" style="background:#00a3e0">Columbia<br>299C</div>
    <div class="swatch" style="background:#00b5e2">Bright Blue<br>306C</div>
  </div>
  <div class="swatches" style="top:241px">
    <div class="swatch" style="background:#4e3629">Brown<br>476C</div>
    <div class="swatch" style="background:#1b3022">Dark Green<br>5535C</div>
    <div class="swatch" style="background:#00843d">Kelly Green<br>348C</div>
    <div class="swatch" style="background:#8bd13f">Bright<br>Green<br>375C</div>
    <div class="swatch" style="background:#a08a4a">Vegas<br>Gold<br>4505C</div>
    <div class="swatch" style="background:#c35a27">Texas<br>Orange<br>1525C</div>
    <div class="swatch" style="background:#f15a24">Bright<br>Orange<br>021C</div>
    <div class="swatch" style="background:#f04e23">Orange<br>172C</div>
    <div class="swatch" style="background:#fbb514">Gold<br>1235C</div>
    <div class="swatch light" style="background:#fee000;border:none">Yellow<br>YellowC</div>
    <div class="swatch light" style="background:#fff">White</div>
  </div>

  <div class="section-bar sub" style="top:281px">Available Colors:<br>Stretch</div>
  <div class="swatches" style="top:304px">
    <div class="swatch" style="background:#000">Black</div>
    <div class="swatch" style="background:#9aa0a6">Gray<br>7543C</div>
    <div class="swatch" style="background:#b0202e">Red<br>187C</div>
    <div class="swatch" style="background:#f49ac1">Pink<br>1905C</div>
    <div class="swatch" style="background:#1b365d">Navy<br>654C</div>
    <div class="swatch" style="background:#1e3f8f">Royal<br>287C</div>
    <div class="swatch" style="background:#fbb514">Gold<br>1235C</div>
    <div class="swatch light" style="background:#fee000;border:none">Yellow<br>YellowC</div>
    <div class="swatch light" style="background:#fff">White</div>
  </div>
  <span class="page-mark right"></span>
</section>

<!-- Spread 3: names & numbers -->
<section class="page page-3">
  <svg class="bg-shapes" viewBox="0 0 451 351" aria-hidden="true">
    <polygon points="190,0 451,0 451,40 190,150" fill="var(--teal)"/>
  </svg>
  <div class="photo" role="img" aria-label="Blue mesh jersey printed with a name and number" style="left:0;top:0;width:212px;height:248px;background:linear-gradient(160deg,#ececec 0%,#2b4fb0 30%,#1d3a94 80%,#222 100%)"></div>
  <div class="photo" role="img" aria-label="Football team huddle in red numbered jerseys" style="left:212px;top:75px;width:239px;height:173px;background:linear-gradient(180deg,#d8453e 0%,#c62e2a 45%,#e6e6e6 80%,#cfcfcf 100%)"></div>
  <h1 class="feature-title" style="top:21px;right:28px;font-size:15.5px;line-height:16px">
    <span>NAMES</span><br><span>AND</span><br><span>NUMBERS</span>
  </h1>
  <div class="feature-band" style="top:248px;height:71px">
    <h2 style="font-size:17px;line-height:22px">TESTED AND PROVEN<br>ON THE FIELD</h2>
    <p style="width:185px;font-size:6.6px">Our Stock numbers and Custom names options are offered in our Varsity product which allows versatility, opacity and durability. We offer numbers in two (2) different styles and four (4) different sizes to help fulfill your sports team needs.</p>
  </div>
  <span class="page-mark left"></span>
</section>

<!-- Spread 4: numbers pricing -->
<section class="page page-4">
  <div class="section-bar main">Sizing &amp; Pricing</div>
  <div class="digits solid" style="left:26px"><span>0</span><span>1</span><span>2</span><span>3</span><span>4</span><span>5</span><span>6</span><span>7</span><span>8</span><span class="last">9</span></div>
  <div class="digits outlined" style="left:162px"><span>0</span><span>1</span><span>2</span><span>3</span><span>4</span><span>5</span><span>6</span><span>7</span><span>8</span><span class="last">9</span></div>

  <div class="origin-badge" role="img" aria-label="Made-in-country badge"></div>

  <table class="kit-table">
    <tr><th>SIZE</th><th>5 PACK</th><th>170pc kit</th><th>340pc kit</th></tr>
    <tr><td>4"</td><td>$0.60</td><td>$18.70</td><td>$34.00</td></tr>
    <tr><td>6"</td><td>$0.95</td><td>$30.60</td><td>$57.80</td></tr>
    <tr><td>8"</td><td>$1.35</td><td>$44.20</td><td>$85.00</td></tr>
    <tr><td>10"</td><td>$1.95</td><td>$64.60</td><td>$115.60</td></tr>
  </table>

  <div class="section-bar sub" style="top:275px">Available Colors:<br>Stretch</div>
  <div class="swatches" style="top:298px;left:20px;gap:4.5px">
    <div class="swatch" style="background:#000">Black</div>
    <div class="swatch light" style="background:#fff">White</div>
    <div class="swatch" style="background:#b0202e">Red<br>187C</div>
    <div class="swatch" style="background:#fbb514">Gold<br>1235C</div>
    <div class="swatch" style="background:#f04e23">Orange<br>172C</div>
    <div class="swatch" style="background:#1e3f8f">Royal<br>287C</div>
    <div class="swatch" style="background:#1b365d">Navy<br>654C</div>
    <div class="swatch" style="background:#9aa0a6">Gray<br>7543C</div>
  </div>
  <span class="page-mark right"></span>
</section>

<!-- Back cover -->
<section class="page page-5" style="background:var(--teal)">
  <svg class="bg-shapes" viewBox="0 0 564 438" preserveAspectRatio="none" aria-hidden="true">
    <defs>
      <linearGradient id="coverPurple" x1="0" x2="1"><stop offset="0" stop-color="#3e2a8a"/><stop offset="1" stop-color="#5b3a9e"/></linearGradient>
    </defs>
    <polygon points="14,0 372,0 430,70 44,90" fill="url(#coverPurple)"/>
    <polygon points="44,90 430,70 564,50 564,345 155,370" fill="#fff"/>
    <polygon points="150,370 564,346 564,438 160,438" fill="url(#coverPurple)"/>
  </svg>
  <div class="brand"><span class="mark"></span><span class="name">Northline Prints</span></div>
  <div class="tagline">Quality Heat Transfers</div>
  <div class="contact">&#9742; 1-800-555-0147 &nbsp;|&nbsp; www.northlineprints.com</div>
</section>

</body>
</html>
```